We have an feature in our CRM to produce online proposals but at the moment they look very boring and plain. We need fresh new exciting designs for them that look highly professional.
We will be choosing 5 designs to use as templates so our users can upload their logo, photos and select their colours so that it generates a professional looking proposal for them.

Here is a sample of one of the existing proposals. All the information that's in the proposal will be used:

https://www.korvelhomes.com.au/portal/proposal.aspx?id=2736&passcode=QWPLMN52&preview=1

One suggestion is to include compelling background images of houses. Also need to show a proposal date at the start of the document along with something that says 'This proposal is valid for 30 days'

```html
<!DOCTYPE html>
<html lang="en">
<head>
<meta charset="utf-8">
<title>Property Proposal – 8502 Magnolia Drive West</title>
<link rel="stylesheet" href="https://fonts.googleapis.com/css2?family=Tinos:wght@400;700&family=Poppins:ital,wght@0,400;0,500;0,600;0,700;1,400;1,500&family=Oswald:wght@500&display=swap">
<style>
:root{
  --backdrop:#a2a2a2;
  --paper:#ffffff;
  --blue:#0b3fa8;
  --blue-deep:#0a35a0;
  --green:#5bb82c;
  --green-text:#3fae2a;
  --ink:#1d1d1f;
  --muted:#4a4a4a;
  --line:#d6d9e2;
  --tint:#f4eff6;
  --card:#f6f6f6;
}
*{box-sizing:border-box;margin:0;padding:0}
html,body{width:1200px;height:2587px;overflow:hidden}
body{background:var(--backdrop);font-family:"Poppins",sans-serif;color:var(--ink);position:relative}
.abs{position:absolute}
.page{position:absolute;background:var(--paper);overflow:hidden}
.page-left{left:62px;top:58px;width:515px;height:2377px}
.page-right{left:616px;top:55px;width:515px;height:1855px}
.serif{font-family:"Tinos",serif}
.photo{position:absolute}
.tiny{font-size:5.6px;line-height:1.75;color:var(--muted)}

/* header & hero */
.brand-bar{left:0;top:0;width:515px;height:49px;background:var(--tint)}
.brand-name{left:0;width:515px;top:22px;text-align:center;font-size:8.5px;color:#1e2a55}
.brand-name .mark{display:inline-block;width:5px;height:5px;background:var(--blue);margin-right:4px;vertical-align:middle}
.hero{left:0;top:49px;width:515px;height:260px;background:linear-gradient(180deg,#c9d3dc 0%,#8d8d86 35%,#4e4a44 70%,#2b2b2d 100%)}
.hero-shade{left:0;top:49px;width:515px;height:260px;background:linear-gradient(180deg,rgba(0,0,0,0) 40%,rgba(10,10,15,.55) 100%)}
.hero-title{left:0;width:515px;top:189px;text-align:center;color:#fff;font-weight:700;font-size:15.5px;line-height:19px}
.hero-date{left:0;width:515px;top:234px;text-align:center;color:#fff;font-size:13px}
.hero-date span{color:var(--green)}
.hero-valid{left:0;width:515px;top:265px;text-align:center;color:#fff;font-size:8px}

/* letter */
.letter-photo{left:243px;top:309px;width:272px;height:175px;background:linear-gradient(90deg,#fff 0%,rgba(255,255,255,.2) 30%,rgba(255,255,255,0) 50%),linear-gradient(180deg,#dde4ea 0%,#e9ecee 45%,#c9c9c4 100%)}
.letter{left:29px;top:325px;width:216px;font-size:5.6px;line-height:1.85;color:var(--muted)}
.letter p{margin-bottom:8px}

/* property card */
.prop-card{left:29px;top:490px;width:458px;height:226px;border:1px solid var(--line);background:#fff}
.prop-photo{left:6px;top:7px;width:228px;height:212px;background:linear-gradient(180deg,#f4a27a 0%,#c9b0c6 30%,#8f6a55 52%,#3aa0d6 70%,#1f7fc4 100%)}
.prop-title{left:259px;top:12px;font-size:15px;font-weight:700;line-height:18px}
.spec{position:absolute;left:255px;width:187px;height:22px;border-bottom:1px solid var(--line);font-size:7.5px;display:flex;align-items:center;color:#333}
.spec svg{width:18px;height:14px;margin-right:8px}
.spec .count{margin-left:auto;width:20px;height:13px;background:var(--blue);color:#fff;font-size:7px;text-align:center;line-height:13px}
.land-btn{left:255px;top:185px;width:187px;height:21px;background:var(--blue);color:#fff;font-size:7px;line-height:21px;padding-left:27px}

/* section headings */
.section-head{left:0;width:515px;text-align:center;font-family:"Tinos",serif;font-weight:700;font-size:23.5px;line-height:30px;color:var(--ink)}
.section-head .rule{display:inline-block;width:36px;height:1px;background:var(--blue);vertical-align:middle;margin:0 6px}

/* sold cards */
.sold-card{position:absolute;width:144px;height:237px;background:var(--card);box-shadow:0 1px 3px rgba(0,0,0,.18)}
.diamond-wrap{position:absolute;left:22px;top:-2px;width:100px;height:100px;transform:translateY(20px) rotate(45deg);background:#fff;box-shadow:0 2px 5px rgba(0,0,0,.25)}
.diamond{position:absolute;left:4px;top:4px;right:4px;bottom:4px}
.sold-name{position:absolute;left:0;width:144px;top:149px;text-align:center;font-size:7.3px;font-weight:600;color:var(--blue)}
.sold-sub{position:absolute;left:0;width:144px;top:160px;text-align:center;font-size:5.8px;color:#333}
.feat{position:absolute;left:0;width:144px;top:175px;display:flex;justify-content:center;gap:9px;font-size:6px;color:#333}
.feat span{display:flex;align-items:center;gap:2px}
.feat svg{width:11px;height:8px}
.sold-line{position:absolute;left:0;width:144px;text-align:center;font-size:6px;color:#333}
.sold-line b{font-weight:500;color:var(--blue)}
.sold-line i{font-style:normal;border:1px solid #ddd;padding:0 2px;background:#fff}

/* listing cards */
.list-card{position:absolute;width:141px;height:187px;background:#fff;box-shadow:0 1px 3px rgba(0,0,0,.16)}
.list-photo{position:absolute;left:4px;top:3px;width:133px;height:98px}
.list-name{position:absolute;left:9px;top:110px;width:128px;font-size:6.3px;color:var(--blue);white-space:nowrap;overflow:hidden}
.list-card .feat{left:9px;width:auto;top:128px;justify-content:flex-start}
.list-line{position:absolute;left:9px;width:126px;font-size:6px;color:#333;line-height:1.35}
.list-line b{font-weight:500;color:var(--blue)}

/* market trends */
.trends{left:0;top:1900px;width:515px;height:245px;background:linear-gradient(180deg,#27375a 0%,#1f2a44 50%,#2a2620 100%)}
.trends-head{top:1938px;color:#fff}
.trends-head .rule{background:#fff}
.trends-copy{left:34px;top:1984px;width:447px;text-align:center;font-size:6.1px;line-height:1.9;color:#fff}

/* indicative value */
.value-accent{left:59px;top:2183px;width:40px;height:40px;background:var(--blue)}
.value-box{left:63px;top:2187px;width:389px;height:168px;background:#fff;border:1px solid var(--blue)}
.value-inner{left:70px;top:2193px;width:375px;height:156px;border:1px solid #c9d2ea}
.value-head{top:2216px}
.value-copy{left:70px;top:2251px;width:375px;text-align:center;font-size:5.6px;line-height:2.1;color:#333}
.value-figure{left:0;width:515px;top:2283px;text-align:center;font-size:28px;font-weight:700;color:var(--blue)}
.value-rec{left:0;width:515px;top:2326px;text-align:center;font-size:8px;color:#222}

/* right page */
.frame{position:absolute;border:1px solid var(--blue)}
.pa-head{left:214px;top:42px;font-size:25px;font-weight:700;font-family:"Tinos",serif}
.pa-head .rule,.prep-head .rule{display:inline-block;width:36px;height:1px;background:var(--blue);vertical-align:middle;margin-left:4px}
.pa-copy{left:197px;top:80px;width:292px}
.bullet{position:relative;padding-left:20px;margin-top:9px}
.bullet svg{position:absolute;left:3px;top:1px;width:11px;height:11px}
.prep-head{left:29px;top:228px;font-size:25px;font-weight:700;font-family:"Tinos",serif}
.prep-copy{left:29px;top:266px;width:302px}
.prep-copy .bullet{margin-top:9px}
.prep-copy .bullet strong{color:var(--blue);font-weight:500;font-size:8px}
.prep-photo{left:351px;top:256px;width:139px;height:224px;background:linear-gradient(180deg,#8fb6e0 0%,#cfd9e3 30%,#9aa2a8 50%,#3c8fbd 70%,#a8c0c8 100%)}
.pool-wash{left:0;top:500px;width:515px;height:170px;background:linear-gradient(180deg,rgba(255,255,255,0) 0%,rgba(210,224,236,.55) 40%,rgba(255,255,255,0) 100%)}
.mkt-head{top:646px}
.mkt-copy{left:30px;top:689px;width:455px;text-align:center}
.mkt-copy p{margin-bottom:9px}
.pkg-prompt{left:0;width:515px;top:810px;text-align:center;font-size:9.5px;font-weight:500;color:#222}
.house-wash{left:0;top:880px;width:515px;height:380px;background:linear-gradient(180deg,rgba(255,255,255,0) 0%,rgba(196,210,220,.55) 30%,rgba(180,190,196,.5) 65%,rgba(255,255,255,0) 100%)}
.pkg-card{position:absolute;background:#fff;border-radius:6px;box-shadow:0 1px 6px rgba(0,0,0,.2)}
.pkg-ribbon{position:absolute;height:31px;background:var(--blue);color:#fff;font-size:13.5px;font-weight:500;display:flex;align-items:center;padding-left:34px;clip-path:polygon(0 0,100% 0,97% 50%,100% 100%,0 100%,3% 50%)}
.pkg-ribbon::before{content:"";position:absolute;left:15px;top:10px;width:11px;height:11px;border-radius:50%;background:var(--green)}
.pkg-list{position:absolute;left:26px;top:62px;width:190px;list-style:none;font-size:6.6px;color:#222}
.pkg-list li{position:relative;padding-left:11px;margin-bottom:5.5px;line-height:1.25}
.pkg-list li::before{content:"";position:absolute;left:0;top:0;width:6px;height:6px;border:1px solid var(--green);border-radius:50%}
.opt-prompt{left:0;width:515px;top:1049px;text-align:center;font-size:10px;line-height:13px;color:#222}
.opts{left:33px;top:1097px;width:470px;display:flex;gap:13px;font-size:10px;color:var(--blue);font-weight:500}
.opts span{display:flex;align-items:center;gap:4px}
.opts span::before{content:"";width:8px;height:8px;border:1px solid var(--green)}
.commission{left:63px;top:1153px;width:389px;height:168px;background:var(--blue);box-shadow:0 0 0 1px #c8d3ee}
.commission-frame{left:66px;top:1156px;width:383px;height:162px;border:1px solid rgba(255,255,255,.9)}
.com-head{top:1182px;color:#fff}
.com-head .rule{background:#fff;width:36px}
.com-copy{left:63px;top:1218px;width:389px;text-align:center;font-size:5.6px;line-height:2.1;color:#fff}
.com-rate{left:63px;top:1246px;width:389px;text-align:center;font-size:26px;font-weight:700;color:#fff}
.com-note{left:63px;top:1279px;width:389px;text-align:center;font-size:5.3px;color:#fff}
.green-rule{left:29px;top:1364px;width:458px;height:4px;background:var(--green)}
.disc-head{left:0;width:515px;top:1389px;text-align:center;font-family:"Tinos",serif;font-weight:700;font-size:21px;color:var(--blue)}
.disc-copy{left:34px;top:1427px;width:450px;text-align:center;font-style:italic;font-size:5.6px;line-height:1.9;color:#444}
.disc-copy p{margin-bottom:10px}
.agent{left:0;top:1560px;width:515px;height:295px;background:var(--blue)}
.agent-ring{left:10px;top:1567px;width:186px;height:186px;border-radius:50%;border:6px solid var(--green);border-right-color:transparent;border-bottom-color:transparent;transform:rotate(-20deg)}
.agent-photo{left:27px;top:1576px;width:172px;height:172px;border-radius:50%;background:linear-gradient(180deg,#e7e3e3 0%,#c8b8b6 50%,#7d6e6c 100%)}
.agent-head{left:216px;top:1581px;font-family:"Tinos",serif;font-weight:700;font-size:21px;color:#fff}
.agent-bio{left:219px;top:1618px;width:270px;font-size:5.6px;line-height:1.85;color:#fff}
.agent-bio p{margin-bottom:7px}
.agent-name{left:35px;top:1763px;font-style:italic;font-weight:500;font-size:16px;color:var(--green)}
.agent-contact{left:34px;top:1801px;font-style:italic;font-size:9px;line-height:13px;color:#fff}
.btn{position:absolute;left:210px;width:235px;height:30px;border-radius:15px;font-family:"Oswald",sans-serif;font-size:16px;color:#fff;text-align:center;line-height:29px}
.btn-accept{top:1768px;background:var(--green)}
.btn-call{top:1811px;border:1.5px solid #fff}
</style>
</head>
<body>

<svg width="0" height="0" style="position:absolute" aria-hidden="true">
  <symbol id="ico-bed" viewBox="0 0 22 14"><rect x="1" y="5" width="20" height="5" fill="currentColor"/><rect x="3" y="2" width="6" height="3" rx="1" fill="currentColor"/><rect x="1" y="10" width="2" height="3" fill="currentColor"/><rect x="19" y="10" width="2" height="3" fill="currentColor"/></symbol>
  <symbol id="ico-bath" viewBox="0 0 22 14"><path d="M2 7h18v2a4 4 0 0 1-4 4H6a4 4 0 0 1-4-4z" fill="currentColor"/><path d="M5 7V2a1.5 1.5 0 0 1 3 0" stroke="currentColor" stroke-width="1.4" fill="none"/></symbol>
  <symbol id="ico-car" viewBox="0 0 22 14"><path d="M5 3h12l3 5v4h-3v-2H5v2H2V8z" fill="currentColor"/><rect x="7" y="4.5" width="8" height="3" fill="#fff"/></symbol>
  <symbol id="ico-diamond" viewBox="0 0 12 12"><rect x="2" y="2" width="8" height="8" transform="rotate(45 6 6)" fill="none" stroke="#0b3fa8" stroke-width="1"/><rect x="4" y="4" width="4" height="4" transform="rotate(45 6 6)" fill="#5bb82c"/></symbol>
</svg>

<!-- ===== LEFT PAGE ===== -->
<main class="page page-left">
  <div class="abs brand-bar"></div>
  <div class="abs brand-name"><span class="mark"></span>Your Agency</div>

  <div class="photo hero" role="img" aria-label="Modern two-storey home with palm trees at dusk"></div>
  <div class="abs hero-shade"></div>
  <h1 class="abs hero-title serif">Proposal for 8502 Magnolia Drive West<br>HOPE ISLAND QLD</h1>
  <div class="abs hero-date">Proposal Date: <span>August 14, 2025</span></div>
  <div class="abs hero-valid">This proposal is valid for 30 days</div>

  <div class="photo letter-photo" role="img" aria-label="White contemporary house facade, faded into the page"></div>
  <div class="abs letter">
    <p>Dear Owen,</p>
    <p>Everyone likes to know what's happening in the property market in their suburb. One of the foundations of understanding your property's value is knowing what sale prices have recently been achieved.</p>
    <p>Knowledge is power and while there are multiple factors that play a role in determining current market value, surrounding sales provide valuable in-sight.</p>
    <p>Below we have listed some recent sales in the area to help you stay informed. If you're interested in a valuation update specific to your property,</p>
  </div>

  <section class="abs prop-card">
    <div class="photo prop-photo" role="img" aria-label="Courtyard home with pool under a sunset sky"></div>
    <h2 class="abs prop-title serif">8502 Magnolia Drive West<br>HOPE ISLAND QLD</h2>
    <div class="spec" style="top:74px"><svg style="color:var(--blue)"><use href="#ico-bed"/></svg>Bedrooms<span class="count">4</span></div>
    <div class="spec" style="top:102px"><svg style="color:var(--blue)"><use href="#ico-bath"/></svg>Bathrooms<span class="count">2</span></div>
    <div class="spec" style="top:130px"><svg style="color:var(--blue)"><use href="#ico-car"/></svg>Garage Spaces<span class="count">2</span></div>
    <div class="abs land-btn">Land Size 1,674 Square Metres</div>
  </section>

  <h2 class="abs section-head" style="top:770px"><span class="rule"></span>Previous Sales in Your Area<span class="rule"></span></h2>

  <!-- sold row 1 -->
  <article class="sold-card" style="left:27px;top:842px">
    <div class="diamond-wrap"><div class="diamond" role="img" aria-label="Modern white home" style="background:linear-gradient(135deg,#9cc3ea,#dfe3e6 50%,#8a8a8a)"></div></div>
    <div class="sold-name">45 RIVERBEND BOULEVARD</div><div class="sold-sub">HELENSVALE</div>
    <div class="feat"><span><svg style="color:var(--blue)"><use href="#ico-bed"/></svg>4</span><span><svg style="color:var(--blue)"><use href="#ico-bath"/></svg>3</span><span><svg style="color:var(--blue)"><use href="#ico-car"/></svg>4</span></div>
    <div class="sold-line" style="top:197px"><b>Sold for :</b> <i>*$1,650,000</i></div>
    <div class="sold-line" style="top:213px"><b>Sold on :</b> 14/07/2025</div>
  </article>
  <article class="sold-card" style="left:185px;top:842px">
    <div class="diamond-wrap"><div class="diamond" role="img" aria-label="Aerial view of green suburb" style="background:linear-gradient(135deg,#bcd6ee,#7fa66a 50%,#4d6b3c)"></div></div>
    <div class="sold-name">79 THE HEADLAND</div><div class="sold-sub">HELENSVALE</div>
    <div class="feat"><span><svg style="color:var(--blue)"><use href="#ico-bed"/></svg>4</span><span><svg style="color:var(--blue)"><use href="#ico-bath"/></svg>2</span><span><svg style="color:var(--blue)"><use href="#ico-car"/></svg>4</span></div>
    <div class="sold-line" style="top:197px"><b>Sold for :</b> <i>$1,750,000</i></div>
    <div class="sold-line" style="top:213px"><b>Sold on :</b> 15/02/2025</div>
  </article>
  <article class="sold-card" style="left:343px;top:842px">
    <div class="diamond-wrap"><div class="diamond" role="img" aria-label="Aerial view of tiled roof home among trees" style="background:linear-gradient(135deg,#3f6d3a,#b86a4b 50%,#56763d)"></div></div>
    <div class="sold-name">3153 REEDWATER DRIVE</div><div class="sold-sub">HOPE ISLAND</div>
    <div class="feat"><span><svg style="color:var(--blue)"><use href="#ico-bed"/></svg>4</span><span><svg style="color:var(--blue)"><use href="#ico-bath"/></svg>3</span><span><svg style="color:var(--blue)"><use href="#ico-car"/></svg>2</span></div>
    <div class="sold-line" style="top:197px"><b>Sold for :</b> <i>$1,700,000</i></div>
    <div class="sold-line" style="top:213px"><b>Sold on :</b> 14/07/2025</div>
  </article>

  <!-- sold row 2 -->
  <article class="sold-card" style="left:27px;top:1102px">
    <div class="diamond-wrap"><div class="diamond" role="img" aria-label="Aerial view of waterfront suburb" style="background:linear-gradient(135deg,#8cc0ec,#c7d4dc 50%,#6f7d69)"></div></div>
    <div class="sold-name">46 TIDEWATER TERRACE</div><div class="sold-sub">HELENSVALE</div>
    <div class="feat"><span><svg style="color:var(--blue)"><use href="#ico-bed"/></svg>3</span><span><svg style="color:var(--blue)"><use href="#ico-bath"/></svg>2</span><span><svg style="color:var(--blue)"><use href="#ico-car"/></svg>2</span></div>
    <div class="sold-line" style="top:197px"><b>Sold for :</b> <i>$1,600,000</i></div>
    <div class="sold-line" style="top:213px"><b>Sold on :</b> 23/01/2025</div>
  </article>
  <article class="sold-card" style="left:185px;top:1102px">
    <div class="diamond-wrap"><div class="diamond" role="img" aria-label="Aerial view of homes among trees" style="background:linear-gradient(135deg,#cfdbe6,#8a9a84 50%,#5a6350)"></div></div>
    <div class="sold-name">7 LAKEMERE COURT</div><div class="sold-sub">HELENSVALE</div>
    <div class="feat"><span><svg style="color:var(--blue)"><use href="#ico-bed"/></svg>5</span><span><svg style="color:var(--blue)"><use href="#ico-bath"/></svg>3</span><span><svg style="color:var(--blue)"><use href="#ico-car"/></svg>2</span></div>
    <div class="sold-line" style="top:197px"><b>Sold for :</b> <i>*$1,650,000</i></div>
    <div class="sold-line" style="top:213px"><b>Sold on :</b> 07/08/2025</div>
  </article>
  <article class="sold-card" style="left:343px;top:1102px">
    <div class="diamond-wrap"><div class="diamond" role="img" aria-label="Pool overlooking the water" style="background:linear-gradient(135deg,#5d9fe0,#9ec9e6 50%,#2e7fb5)"></div></div>
    <div class="sold-name">11 WESTBROOK COURT</div><div class="sold-sub">HELENSVALE</div>
    <div class="feat"><span><svg style="color:var(--blue)"><use href="#ico-bed"/></svg>4</span><span><svg style="color:var(--blue)"><use href="#ico-bath"/></svg>3</span><span><svg style="color:var(--blue)"><use href="#ico-car"/></svg>2</span></div>
    <div class="sold-line" style="top:197px"><b>Sold for :</b> <i>$1,850,000</i></div>
    <div class="sold-line" style="top:213px"><b>Sold on :</b> 28/03/2025</div>
  </article>

  <h2 class="abs section-head" style="top:1405px"><span class="rule"></span>Properties on the Market<span class="rule"></span><br>in Your Area</h2>

  <!-- listings row 1 -->
  <article class="list-card" style="left:37px;top:1477px">
    <div class="photo list-photo" role="img" aria-label="Bright living room" style="background:linear-gradient(180deg,#d8d8d4,#b9b3aa 60%,#8d8780)"></div>
    <div class="list-name">79 The Headland Helensvale QL</div>
    <div class="feat"><span><svg style="color:var(--blue)"><use href="#ico-bed"/></svg>4</span><span><svg style="color:var(--blue)"><use href="#ico-bath"/></svg>2</span><span><svg style="color:var(--blue)"><use href="#ico-car"/></svg>3</span></div>
    <div class="list-line" style="top:146px"><b>Listed for :</b> Contact Agent</div>
    <div class="list-line" style="top:158px"><b>Listed on :</b> 07/01/2025</div>
  </article>
  <article class="list-card" style="left:190px;top:1477px">
    <div class="photo list-photo" role="img" aria-label="Home with dark roof at dusk" style="background:linear-gradient(180deg,#8fb2d9,#4c5d75 45%,#c89c6a 80%,#7b7e84)"></div>
    <div class="list-name">2 Boatmans Court Helensvale ...</div>
    <div class="feat"><span><svg style="color:var(--blue)"><use href="#ico-bed"/></svg>4</span><span><svg style="color:var(--blue)"><use href="#ico-bath"/></svg>3</span><span><svg style="color:var(--blue)"><use href="#ico-car"/></svg>2</span></div>
    <div class="list-line" style="top:146px"><b>Listed for :</b> Expressions of Interest</div>
    <div class="list-line" style="top:158px"><b>Listed on :</b> 14/01/2025</div>
  </article>
  <article class="list-card" style="left:342px;top:1477px">
    <div class="photo list-photo" role="img" aria-label="Two-storey home with pool" style="background:linear-gradient(180deg,#a9c4e6,#d7b49a 45%,#b07e5c 65%,#3e9ed8)"></div>
    <div class="list-name">30 Harbour Vale Drive Helensval..</div>
    <div class="feat"><span><svg style="color:var(--blue)"><use href="#ico-bed"/></svg>4</span><span><svg style="color:var(--blue)"><use href="#ico-bath"/></svg>2</span><span><svg style="color:var(--blue)"><use href="#ico-car"/></svg>2</span></div>
    <div class="list-line" style="top:146px"><b>Listed for :</b> JUST LISTED! WATER VIEWS! SIDE ACCESS!</div>
    <div class="list-line" style="top:167px"><b>Listed on :</b> 11/08/2025</div>
  </article>

  <!-- listings row 2 -->
  <article class="list-card" style="left:37px;top:1677px">
    <div class="photo list-photo" role="img" aria-label="Modern home with pool at dusk" style="background:linear-gradient(180deg,#8ea7c4,#575d66 45%,#d9b98d 70%,#4aa1d2)"></div>
    <div class="list-name">534 Pearl Cove Promenade ..</div>
    <div class="feat"><span><svg style="color:var(--blue)"><use href="#ico-bed"/></svg>4</span><span><svg style="color:var(--blue)"><use href="#ico-bath"/></svg>2</span><span><svg style="color:var(--blue)"><use href="#ico-car"/></svg>2</span></div>
    <div class="list-line" style="top:146px"><b>Listed for :</b> Offers Over $1.65mil</div>
    <div class="list-line" style="top:158px"><b>Listed on :</b> 18/06/2025</div>
  </article>
  <article class="list-card" style="left:190px;top:1677px">
    <div class="photo list-photo" role="img" aria-label="Pool with garden and umbrella" style="background:linear-gradient(180deg,#6f9a6a,#a9c08f 40%,#2fb1c8 75%,#7fd0da)"></div>
    <div class="list-name">35 Parkside Road Helen..</div>
    <div class="feat"><span><svg style="color:var(--blue)"><use href="#ico-bed"/></svg>5</span><span><svg style="color:var(--blue)"><use href="#ico-bath"/></svg>3</span><span><svg style="color:var(--blue)"><use href="#ico-car"/></svg>2</span></div>
    <div class="list-line" style="top:146px"><b>Listed for :</b> $1,650,000</div>
    <div class="list-line" style="top:158px"><b>Listed on :</b> 19/06/2025</div>
  </article>
  <article class="list-card" style="left:342px;top:1677px">
    <div class="photo list-photo" role="img" aria-label="Living room with sofas" style="background:linear-gradient(180deg,#dcd6cc,#bfae98 55%,#8b7a66)"></div>
    <div class="list-name">5217 Seaview Drive West Hope...</div>
    <div class="feat"><span><svg style="color:var(--blue)"><use href="#ico-bed"/></svg>3</span><span><svg style="color:var(--blue)"><use href="#ico-bath"/></svg>2</span><span><svg style="color:var(--blue)"><use href="#ico-car"/></svg>1</span></div>
    <div class="list-line" style="top:146px"><b>Listed for :</b> Asking Price $1,795,000</div>
    <div class="list-line" style="top:167px"><b>Listed on :</b> 13/01/2025</div>
  </article>

  <section class="photo trends" role="img" aria-label="Homes at dusk, darkened behind text"></section>
  <h2 class="abs section-head trends-head"><span class="rule"></span>Current Market Trends<span class="rule"></span></h2>
  <p class="abs trends-copy">Hope Island's real estate market continues to demonstrate strong resilience, particularly in its premium waterfront and lifestyle segments. According to DataCore data via Property Investor Monthly, the current median house price stands at approximately AUD$1.853million, with an annual capital growth rate of 0.00%, and houses now spend an average of 57 days on market. Rental yields hold steady at around 3.72%, supported by a median weekly rent of AUD$1,150. Notably, while quarterly house values have declined by about −3.65%, the 12-month trend remains flat, reflecting a stable yet cautious market environment. In contrast, units have become a standout performer in the Hope Island market. Propertylist.com.au reports that units have posted a robust 7.2% annual growth rate, with median sale prices around AUD 879,000, and rental yields averaging 4.7%—above the house segment. Monthly data reveals that units offer compelling demand: growing median rental prices, shrinking vacancy periods, and strong investor interest. Meanwhile, local historic trends show that well-located 4- and 5-bedroom houses continue to command a premium, with median prices ranging from AUD 2million for 4-beds to AUD 2.77 million for 5-beds, both segments showing double-digit year-on-year growth—9.9% and 19.1% respectively.</p>

  <div class="abs value-accent"></div>
  <div class="abs value-box"></div>
  <div class="abs value-inner"></div>
  <h2 class="abs section-head value-head"><span class="rule"></span>Indicative Value<span class="rule"></span></h2>
  <p class="abs value-copy">Reviewing what similar properties have recently sold along with those that are currently on the market, we estimate the below<br>price range will be achieved for your property.</p>
  <div class="abs value-figure">$1.5 M to $1.8 M</div>
  <div class="abs value-rec">Recommended List Price : Offers over $1.6 M</div>
</main>

<!-- ===== RIGHT PAGE ===== -->
<main class="page page-right">
  <div class="frame" style="left:21px;top:37px;width:138px;height:148px"></div>
  <div class="photo" role="img" aria-label="Two-storey house with pool and deck" style="left:29px;top:43px;width:138px;height:148px;background:linear-gradient(180deg,#9cc0e8 0%,#5a6673 35%,#d7b28a 65%,#e9e6e0 100%)"></div>
  <h2 class="abs pa-head">Property Analysis<span class="rule"></span></h2>
  <div class="abs pa-copy tiny">
    <p>This Price Update is perfect for monitoring the market, however we are able to provide a current market valuation for your property if you're interested. This can be done in two ways:</p>
    <p class="bullet"><svg><use href="#ico-diamond"/></svg>An e-Update which can be emailed to you, however please bear in mind that this will not be validated by an on-site viewing of the property.</p>
    <p class="bullet"><svg><use href="#ico-diamond"/></svg>Alternatively, we can meet at the property to do a full assessment and provide you with a valuation taking into account the location, views, presentation and condition of your property along with recent sales of local homes and our in depth market knowledge.</p>
  </div>

  <div class="photo pool-wash" role="img" aria-label="Pale poolside terrace, faded into the page"></div>
  <h2 class="abs prep-head">Preparation<span class="rule"></span></h2>
  <div class="abs prep-copy tiny">
    <p>To maximise buyer interest and achieve the strongest possible sale price, we recommend a strategic approach to preparing your property for market. Presentation plays a critical role in attracting premium buyers—particularly in Hope Island, where lifestyle appeal and first impressions are paramount.</p>
    <p class="bullet"><svg><use href="#ico-diamond"/></svg><strong>Declutter and Depersonalise</strong> – Remove excess personal items and streamline furniture to create a sense of space and allow buyers to visualise themselves in the property.</p>
    <p class="bullet"><svg><use href="#ico-diamond"/></svg><strong>Professional Styling</strong> – Engage a home stylist to highlight your property's best features, with furniture, artwork and décor selected to appeal to the target market.</p>
    <p class="bullet"><svg><use href="#ico-diamond"/></svg><strong>Minor Repairs &amp; Maintenance</strong> – Address any visible wear and tear, such as paint touch-ups, leaking taps, cracked tiles or weathered timber, to ensure the property presents as well-maintained.</p>
    <p class="bullet"><svg><use href="#ico-diamond"/></svg><strong>Landscaping and Street Appeal</strong> – Invest in fresh mulch, trimmed hedges, mowed lawns, and seasonal flowers to create an inviting entrance. Waterfront properties should ensure pontoons, boardwalks and outdoor living areas are presented in excellent condition.</p>
    <p class="bullet"><svg><use href="#ico-diamond"/></svg><strong>Deep Cleaning</strong> – Engage professional cleaners to ensure all surfaces, windows, carpets and outdoor areas are spotless before photography and open homes.</p>
    <p class="bullet"><svg><use href="#ico-diamond"/></svg><strong>High-Quality Marketing Preparation</strong> – Allow time for professional photography, drone footage, floor plans, and potentially twilight photography to showcase the property in the most appealing light.</p>
    <p style="margin-top:18px">By following these recommendations, we position your property to stand out in the competitive Hope Island market, attract more qualified buyers, and create the conditions for a strong sale result.</p>
  </div>
  <div class="frame" style="left:366px;top:249px;width:130px;height:226px"></div>
  <div class="photo prep-photo" role="img" aria-label="Poolside view of a white two-storey home"></div>

  <div class="photo house-wash" role="img" aria-label="Faded white weatherboard house behind the packages"></div>
  <h2 class="abs section-head mkt-head"><span class="rule"></span>Marketing Strategy<span class="rule"></span></h2>
  <div class="abs mkt-copy tiny">
    <p>Your listing will rotate back to the top of the first page of search results every 15 days. This exposes your listing to more and newer buyers continually.</p>
    <p>With over half of Queenslanders not going past the first page of search results, you'll be seen ahead of almost three quarters of the listings in QLD and give your listing a better chance to get on page one.</p>
    <p>Give buyers a taste of why they should choose your property. Your review will sit below the property description and provide a unique insight into the local area. Community content like this has attracted more than 74M buyers to the site since launching. This exclusive tool can promote your home in a way that no other portal can.</p>
  </div>
  <div class="abs pkg-prompt">Please select a package below...</div>

  <div class="pkg-card" style="left:36px;top:841px;width:218px;height:164px">
    <div class="pkg-ribbon" style="left:12px;top:16px;width:188px">Package 1 - $503.20</div>
    <ul class="pkg-list">
      <li>Major website - propertylist.com.au (premier Plus)</li>
      <li>homefind.com.au (Silver) nestview.com.au (Silver)</li>
      <li>Minor websites -</li>
      <li>Property Ebook</li>
      <li>Professional Photography Package - Photos, Video, Drone and Floorplan</li>
      <li>Signboard</li>
    </ul>
  </div>
  <div class="pkg-card" style="left:268px;top:841px;width:218px;height:72px">
    <div class="pkg-ribbon" style="left:12px;top:15px;width:191px">Package 2 - $3,000</div>
  </div>

  <div class="abs opt-prompt">Please select any of the following options you would like<br>to be included in your marketing campaign:</div>
  <div class="abs opts"><span>asdf - $0</span><span>sign board - $150</span><span>Mail Out - $140</span><span>Done photography - $550</span></div>

  <section class="abs commission"></section>
  <div class="abs commission-frame"></div>
  <h2 class="abs section-head com-head"><span class="rule"></span>Commission Structure<span class="rule"></span></h2>
  <p class="abs com-copy">Portal costs are based on your location and the density of the area, PLA calculates this cost.<br>We pass this directly on to you with no add-on costs.</p>
  <div class="abs com-rate">4.3 %</div>
  <div class="abs com-note">* commission quoted is inclusive GST</div>

  <div class="abs green-rule"></div>
  <h2 class="abs disc-head">Disclaimer</h2>
  <div class="abs disc-copy">
    <p>The information displayed in this document may be based on historical and current data supplied to Marketlens Pty Ltd by third parties including State government agencies and constitutes "Third Party Data" or "Third Party Information". Marketlens does not make any warranty as to the accuracy, completeness or reliability of the information or accept any liability arising in any way from any omissions or errors in this information. The information should not be regarded as advice or relied upon by you or any other person and Marketlens recommend that you seek professional advice before making any property decisions.</p>
    <p>Based on or contains data provided by the State of Queensland (Department of Natural Resources and Mines) 2017. In consideration of the State permitting the use of this data you acknowledge and agree that the State gives no warranty in relation to the data (including accuracy, reliability, completeness, currency or suitability) and accepts no liability (including without limitation, liability in negligence) for any loss, damage or costs (including consequential damage) relating to any use of the data. Data must not be used for direct marketing or be used in breach of privacy laws.</p>
  </div>

  <section class="abs agent"></section>
  <div class="abs agent-ring"></div>
  <div class="photo agent-photo" role="img" aria-label="Portrait photo of the agent"></div>
  <h2 class="abs agent-head">Your Agent</h2>
  <div class="abs agent-bio">
    <p>Liam is dedicated to achieving outstanding results and is committed to helping his clients achieve their goals. With an impressive record of past sales and satisfied clients, Liam continues to be driven by the satisfaction he receives from negotiating and delivering results above expectations. Previous time spent in the building industry selling new homes has given Liam comprehensive knowledge of this specialised area.</p>
    <p>Quality and focus on client care are the keys to Liam's success in delivering a high level of personal attention. Liam's strengths lie in knowing these markets inside and out and having a proactive and<br>strategic approach to selling and caring about the long-term welfare of his clients.<br>As an integral part of Your Agency Realtor with its proven industry leadership, business philosophies and exceptional marketing tools, Liam possesses everything necessary to assist him in achieving excellent results for his clients.</p>
  </div>
  <div class="abs agent-name">Liam Carver</div>
  <div class="abs agent-contact">Mobile : 0491562837<br>Phone : test<br>liam@korveltech.com.au</div>
  <div class="btn btn-accept">ACCEPT</div>
  <div class="btn btn-call">REQUEST A CALL BACK</div>
</main>

</body>
</html>
```